Ridgeline Journeys business card

please see website
www.ridgelinejourneys.comau

info needed on card
Curtis Halvey
Ph
email
Adventure Riding GPS trails

please use my logo and colours off my site

Curtis Halvey
curtis@ridgelinejourneys.com

```html
<!DOCTYPE html>
<html lang="en">
<head>
<meta charset="utf-8">
<title>Ridgeline Journeys business card</title>
<link href="https://fonts.googleapis.com/css2?family=Source+Sans+3:ital,wght@0,400;0,600;0,700;1,400;1,600&display=swap" rel="stylesheet">
<style>
  :root {
    --backdrop: #4a4a4a;
    --ink-black: #000000;
    --paper: #f4f4f4;
    --text-dark: #2b2b2b;
    --text-mid: #444444;
    --accent-yellow: #f2e21a;
    --dash-grey: #3a3a3a;
    --dash-light: #e6e6e6;
  }
  * { box-sizing: border-box; margin: 0; padding: 0; }
  html, body {
    width: 1200px;
    height: 750px;
    overflow: hidden;
    background: var(--backdrop);
    font-family: "Source Sans 3", "Myriad Pro", sans-serif;
  }
  .card {
    position: absolute;
    left: 371px;
    width: 461px;
    height: 263px;
    overflow: hidden;
  }
  /* Front face */
  .card-front { top: 99px; background: var(--paper); }
  .front-band {
    position: absolute;
    left: 0; top: 0;
    width: 100%;
    height: 62px;
    background: var(--ink-black);
  }
  .holder-name {
    position: absolute;
    right: 26px;
    top: 23px;
    font-size: 17px;
    font-weight: 600;
    color: var(--accent-yellow);
  }
  .dash-stripe {
    position: absolute;
    left: 0; top: 62px;
    width: 100%;
    height: 8px;
    background: var(--dash-light);
  }
  .dash-stripe svg { display: block; }
  .brand-lockup {
    position: absolute;
    left: 28px;
    top: 108px;
    display: flex;
    align-items: center;
    gap: 12px;
  }
  .brand-dot {
    width: 30px;
    height: 30px;
    border-radius: 50%;
    background: var(--accent-yellow);
  }
  .brand-name {
    font-size: 26px;
    font-weight: 700;
    color: var(--text-dark);
    line-height: 1;
  }
  .contact-list {
    position: absolute;
    left: 25px;
    top: 190px;
    list-style: none;
  }
  .contact-list li {
    display: flex;
    align-items: center;
    gap: 6px;
    height: 18.5px;
    font-size: 11.5px;
    color: var(--text-mid);
  }
  .contact-list svg { width: 12px; height: 12px; flex: none; }
  .tagline {
    position: absolute;
    right: 26px;
    top: 226px;
    font-size: 13px;
    font-style: italic;
    font-weight: 600;
    color: var(--text-mid);
  }
  /* Back face */
  .card-back { top: 381px; background: var(--ink-black); }
  .back-lockup {
    position: absolute;
    left: 0; right: 0;
    top: 112px;
    display: flex;
    justify-content: center;
    align-items: center;
    gap: 12px;
  }
  .back-lockup .brand-name { color: var(--accent-yellow); font-size: 28px; }
  .back-url {
    position: absolute;
    left: 0; right: 0;
    top: 216px;
    text-align: center;
    font-size: 11.5px;
    font-style: italic;
    color: var(--accent-yellow);
  }
</style>
</head>
<body>
  <section class="card card-front">
    <div class="front-band">
      <p class="holder-name">Curtis Halvey</p>
    </div>
    <div class="dash-stripe">
      <svg width="461" height="8" viewBox="0 0 461 8">
        <line x1="0" y1="4" x2="461" y2="4" stroke="var(--dash-grey)" stroke-width="4" stroke-dasharray="15 4"/>
      </svg>
    </div>

    <div class="brand-lockup">
      <span class="brand-dot"></span>
      <span class="brand-name">Ridgeline Journeys</span>
    </div>

    <ul class="contact-list">
      <li>
        <svg viewBox="0 0 12 12" aria-hidden="true"><path d="M2.2 1 L4.3 1 L5 3.6 L3.8 4.6 C4.5 6.2 5.8 7.5 7.4 8.2 L8.4 7 L11 7.7 L11 9.8 C11 10.5 10.4 11 9.7 11 C5 10.7 1.3 7 1 2.3 C1 1.6 1.5 1 2.2 1 Z" fill="var(--text-dark)"/></svg>
        <span>612 555 0148</span>
      </li>
      <li>
        <svg viewBox="0 0 12 12" aria-hidden="true"><rect x="0.5" y="2.5" width="11" height="7.5" fill="var(--text-dark)"/><path d="M1 3 L6 7 L11 3" fill="none" stroke="var(--paper)" stroke-width="1"/></svg>
        <span>curtis@ridgelinejourneys.com</span>
      </li>
      <li>
        <svg viewBox="0 0 12 12" aria-hidden="true"><circle cx="6" cy="6" r="5.5" fill="var(--text-dark)"/><path d="M3 3.5 C4.5 3 5.5 4.5 4.5 5.5 C3.5 6.5 4.5 8 5.5 8.5 M7.5 2 C8 3.5 9.5 3.5 10 5 C9 6 8 7 8.5 9" fill="none" stroke="var(--paper)" stroke-width="1"/></svg>
        <span>www.ridgelinejourneys.com.au</span>
      </li>
    </ul>

    <p class="tagline">Adventure Riding GPS trails</p>
  </section>

  <section class="card card-back">
    <div class="back-lockup">
      <span class="brand-dot"></span>
      <span class="brand-name">Ridgeline Journeys</span>
    </div>
    <p class="back-url">www.ridgelinejourneys.com.au</p>
  </section>
</body>
</html>
```